Super elegant, crisp & clean Business card design required

We recently upgraded our branding - which is on our website - talvendoraphoto.com

I would like a simple, yet elegant, clean business card design please.

The font of my logo is Cinzel - and because of the natural colour - it's best to have this on a black background.

I would like to have the back of the business card - with simply my logo.

PLEASE DO NOT SUBMIT A COMPLICATED / UNCLEAN DESIGN

Industry/Entity Type

Business

Contact Information for Business Card

Talven Doroshko Photography

Font styles to use
Other font styles liked:
• Cinzel

Requirements
Must have
• A backpage with nothing but my logo
• Simple design - stands out
Should not have
• Colour that dont align with my logo
• Over complicated '/ non symmetrical design

```html
<!DOCTYPE html>
<html lang="en">
<head>
<meta charset="utf-8">
<title>Talven Doroshko Photography — Stationery</title>
<link href="https://fonts.googleapis.com/css2?family=Cinzel:wght@400&family=Questrial&display=swap" rel="stylesheet">
<style>
  :root {
    --backdrop: #d3c9ba;
    --paper: #ffffff;
    --ink-dark: #232320;
    --ink-dark-soft: #2b2b27;
    --gold: #a5876a;
    --gold-muted: #8a7560;
    --shadow: 0 2px 6px rgba(60, 50, 40, 0.25);
  }
  html, body {
    margin: 0;
    padding: 0;
    width: 1200px;
    height: 943px;
    overflow: hidden;
    background: var(--backdrop);
  }
  .canvas {
    position: relative;
    width: 1200px;
    height: 943px;
    background: var(--backdrop);
    font-family: "Cinzel", serif;
  }
  .piece {
    position: absolute;
    box-shadow: var(--shadow);
    box-sizing: border-box;
  }
  .brand {
    position: absolute;
    left: 0;
    right: 0;
    text-align: center;
    color: var(--gold);
    line-height: 1;
  }
  .brand-mark {
    display: block;
    margin: 0 auto;
    border: 1px solid var(--gold);
    border-radius: 50%;
  }
  .brand-name {
    display: block;
    font-family: "Cinzel", serif;
    font-weight: 400;
    white-space: nowrap;
  }
  .brand-tag {
    display: block;
    font-family: "Cinzel", serif;
    font-weight: 400;
    white-space: nowrap;
  }

  /* Letterhead */
  .letterhead {
    left: 74px; top: 114px; width: 350px; height: 494px;
    background: var(--paper);
  }
  .letterhead .brand { top: 26px; }
  .letterhead .brand-mark { width: 22px; height: 22px; margin-bottom: 8px; }
  .letterhead .brand-name { font-size: 9.5px; letter-spacing: 0.2px; }
  .letterhead .brand-tag { font-size: 3.6px; letter-spacing: 2.6px; margin-top: 2px; }
  .letterhead-footer {
    position: absolute;
    left: 0; right: 0; bottom: 13px;
    text-align: center;
    font-family: "Questrial", sans-serif;
    font-size: 4.6px;
    line-height: 6.2px;
    color: var(--gold-muted);
  }
  .letterhead-footer strong { font-weight: 400; color: var(--ink-dark); }

  /* Presentation folder */
  .folder {
    left: 464px; top: 113px; width: 350px; height: 495px;
    background: linear-gradient(160deg, var(--ink-dark-soft), var(--ink-dark));
    border-radius: 2px;
  }
  .folder-spine {
    position: absolute;
    left: 7px; top: 0; bottom: 0;
    width: 1px;
    background: rgba(0, 0, 0, 0.45);
  }
  .folder .brand { top: 196px; }
  .folder .brand-mark { width: 40px; height: 40px; margin-bottom: 18px; }
  .folder .brand-name { font-size: 11.5px; letter-spacing: 0.3px; }
  .folder .brand-tag { font-size: 5.6px; letter-spacing: 3.6px; margin-top: 3px; }
  .folder-web {
    position: absolute;
    left: 0; right: 0; bottom: 31px;
    text-align: center;
    font-family: "Questrial", sans-serif;
    font-size: 6.4px;
    color: var(--gold-muted);
  }

  /* Business cards */
  .card {
    width: 150px; height: 82px;
    left: 74px;
    background: linear-gradient(160deg, var(--ink-dark-soft), var(--ink-dark));
  }
  .card-front { top: 648px; }
  .card-back { top: 749px; }
  .card .brand-name { font-size: 6.3px; }
  .card .brand-tag { font-size: 2.8px; letter-spacing: 1.6px; margin-top: 1.5px; }
  .card-front .brand { top: 30px; }
  .card-rule {
    position: absolute;
    left: 40px; right: 40px; top: 45px;
    height: 1px;
    background: rgba(165, 135, 106, 0.3);
  }
  .card-contact {
    position: absolute;
    left: 0; right: 0; top: 50px;
    text-align: center;
    font-family: "Questrial", sans-serif;
    font-size: 3.4px;
    line-height: 4.4px;
    color: var(--gold-muted);
  }
  .card-back .brand { top: 23px; }
  .card-back .brand-mark { width: 16px; height: 16px; margin-bottom: 7px; }

  /* Compliment slip / DL sheet */
  .dl-sheet {
    left: 264px; top: 660px; width: 350px; height: 164px;
    background: linear-gradient(160deg, var(--ink-dark-soft), var(--ink-dark));
  }
  .dl-sheet .brand { left: 25px; right: auto; width: 100px; top: 26px; }
  .dl-sheet .brand-mark { width: 28px; height: 28px; margin-bottom: 8px; }
  .dl-sheet .brand-name { font-size: 7.8px; }
  .dl-sheet .brand-tag { font-size: 3.4px; letter-spacing: 2.2px; margin-top: 2px; }

  /* Envelope */
  .envelope {
    left: 648px; top: 661px; width: 350px; height: 165px;
    background: linear-gradient(175deg, #ffffff, #f1f1f1);
    overflow: hidden;
  }
  .envelope-flap {
    position: absolute;
    left: 0; top: 0;
    width: 350px; height: 50px;
  }
  .envelope .brand { top: 18px; }
  .envelope .brand-name { font-size: 5.6px; }
</style>
</head>
<body>
<main class="canvas">

  <section class="piece letterhead" aria-label="Letterhead">
    <div class="brand">
      <span class="brand-mark"></span>
      <span class="brand-name">Talven Doroshko</span>
      <span class="brand-tag">Photography</span>
    </div>
    <footer class="letterhead-footer">
      <strong>TALVEN DOROSHKO</strong> · PHOTOGRAPHY<br>
      T: 07700 900418 · E: info@talvendoraphoto.com · www.talvendoraphoto.com
    </footer>
  </section>

  <section class="piece folder" aria-label="Presentation folder">
    <div class="folder-spine"></div>
    <div class="brand">
      <span class="brand-mark"></span>
      <span class="brand-name">Talven Doroshko</span>
      <span class="brand-tag">Photography</span>
    </div>
    <div class="folder-web">www.talvendoraphoto.com</div>
  </section>

  <section class="piece card card-front" aria-label="Business card front">
    <div class="brand">
      <span class="brand-name">Talven Doroshko</span>
      <span class="brand-tag">Photography</span>
    </div>
    <div class="card-rule"></div>
    <div class="card-contact">
      T: 07700 900418 · E: info@talvendoraphoto.com<br>
      www.talvendoraphoto.com
    </div>
  </section>

  <section class="piece card card-back" aria-label="Business card back">
    <div class="brand">
      <span class="brand-mark"></span>
      <span class="brand-name">Talven Doroshko</span>
      <span class="brand-tag">Photography</span>
    </div>
  </section>

  <section class="piece dl-sheet" aria-label="Compliment slip">
    <div class="brand">
      <span class="brand-mark"></span>
      <span class="brand-name">Talven Doroshko</span>
      <span class="brand-tag">Photography</span>
    </div>
  </section>

  <section class="piece envelope" aria-label="Envelope">
    <svg class="envelope-flap" viewBox="0 0 350 50" aria-hidden="true">
      <polygon points="0,0 350,0 338,50 12,50" fill="#232320"/>
    </svg>
    <div class="brand">
      <span class="brand-name">Talven Doroshko</span>
    </div>
  </section>

</main>
</body>
</html>
```